KVM Contracting services . Building and maintenance services, optic fibre installation

Business cards and logo design.I need a logo that I can use on business cards ,workwear and on my vehicles. I would like the KVM to be the main or larger text and contracting services to be the smaller or less important text.I like monograms, modern designs and repeating patterns symbols. I am also a Gemini and my favourite number is 22 so if this can be any inspiration to help with the design. Am thinking of the using German flag colours as a his is my family’s heritage. And the other 2 main colours I wear is black and white.But any ideas are appreciated.I do not need a design that is trade specific but a design that could be used for any business.

Target Market(s)

General public

Contact Information for Business Card

KVM Contracting Services ( front of business card)

(Back of business card)
Darren Holtwick
0451907326
Maintenance services
Optic fibre and data installation

Logo Text

Logo can just be pattern or monogram or incorporate KVM . I like the gemini star sign and the number 22

Colors
ec1f27
000000
fbee3e
ffffff

Requirements
Must have
• Logo and KVM Contracting Services on the front of business card
Nice to have
• Possible use of German flag colours.
• Modern design.
• Design to be able to be used on black or white background as I want to put it on clothing

```html
<!DOCTYPE html>
<html lang="en">
<head>
<meta charset="utf-8">
<title>KVM Contracting Services — Business Card</title>
<link rel="stylesheet" href="https://fonts.googleapis.com/css2?family=Montserrat:wght@700;800&family=Michroma&family=Open+Sans:wght@400&display=swap">
<style>
  :root {
    --stage: #282828;
    --card-white: #ffffff;
    --ink: #111111;
    --brand-red: #ec1f27;
    --rule: #b9b9b9;
    --grad-top: #1c1012;
    --grad-deep: #7a0a0c;
    --grad-red: #ff1200;
    --grad-orange: #ff6a00;
    --grad-yellow: #ffb800;
  }
  * { margin: 0; padding: 0; box-sizing: border-box; }
  html, body { width: 1200px; height: 900px; overflow: hidden; }
  body { background: var(--stage); position: relative; font-family: "Open Sans", sans-serif; }

  .card {
    position: absolute;
    top: 275px;
    width: 477px;
    height: 293px;
    box-shadow: 2px 4px 8px rgba(0,0,0,0.55);
  }
  .card--back {
    left: 120px;
    background: var(--card-white);
    border-radius: 0 48px 0 48px;
  }
  .card--front {
    left: 607px;
    height: 291px;
    border-radius: 48px 0 48px 0;
    background: linear-gradient(180deg,
      var(--grad-top) 0%, var(--grad-deep) 22%, var(--grad-red) 50%,
      var(--grad-orange) 75%, var(--grad-yellow) 100%);
  }

  .brand { position: absolute; text-align: center; }
  .brand__name {
    display: block;
    font-family: "Montserrat", sans-serif;
    font-weight: 800;
    line-height: 1;
    letter-spacing: 2px;
  }
  .brand__tagline {
    display: block;
    font-family: "Montserrat", sans-serif;
    font-weight: 700;
    text-transform: uppercase;
    white-space: nowrap;
  }

  .card--back .brand { right: 38px; top: 50px; }
  .card--back .brand__name { font-size: 76px; color: var(--ink); text-align: right; }
  .card--back .brand__tagline { font-size: 17.5px; color: var(--ink); margin-top: 6px; }

  .card--front .brand { left: 0; right: 0; top: 90px; }
  .card--front .brand__name { font-size: 92px; color: var(--card-white); }
  .card--front .brand__tagline { font-size: 21px; color: var(--card-white); margin-top: 4px; letter-spacing: 0.5px; }

  .contact { position: absolute; left: 32px; top: 178px; right: 31px; }
  .contact__name {
    font-family: "Michroma", sans-serif;
    font-size: 14.5px;
    color: var(--brand-red);
    text-transform: uppercase;
    letter-spacing: 0.5px;
  }
  .contact__phone-row { display: flex; align-items: center; gap: 5px; margin-top: 1px; }
  .contact__phone { font-size: 16px; color: var(--ink); }
  .contact__rule { flex: 1; height: 1px; background: var(--rule); margin-top: 2px; }

  .services { position: absolute; left: 32px; top: 232px; list-style: none; font-size: 13.5px; color: var(--ink); line-height: 17px; }
</style>
</head>
<body>
  <section class="card card--back" aria-label="Business card, contact side">
    <div class="brand">
      <span class="brand__name">KVM</span>
      <span class="brand__tagline">Contracting Services</span>
    </div>
    <div class="contact">
      <p class="contact__name">Darren Holtwick</p>
      <div class="contact__phone-row">
        <span class="contact__phone">0451907326</span>
        <span class="contact__rule"></span>
      </div>
    </div>
    <ul class="services">
      <li>Maintenance services</li>
      <li>Optic fibre and data installation</li>
    </ul>
  </section>

  <section class="card card--front" aria-label="Business card, brand side">
    <div class="brand">
      <span class="brand__name">KVM</span>
      <span class="brand__tagline">Contracting Services</span>
    </div>
  </section>
</body>
</html>
```